Valdane Companies Business Card Design

We need a new business card for our Private Equity Real Estate Development firm, “Valdane” and our EB-5 regional center “Thornmere Regional Center” on one card. We prefer a design that is simple, elegant, and represents the luxury products we design and build as well as the financial security and stability our successful history has produced. We are an industry leader in our field and 3rd generation family business that has evolved into an institutional quality investment platform. Considered design size is standard business card dimensions (3.5 x 2 inches with an additional 1/8 inch space for design elements or backgrounds that extend beyond the finished size of your piece.

Target Market(s)

• High net worth individuals
• Highly skilled technical workers and physicians in the US seeking investment-based immigration opportunities
• Sophisticated private equity investors
• Intermediary partners include domestic attorneys and investment brokers, as well as international agent networks
• US real estate developers

Industry/Entity Type

Finance

Contact Information for Business Card

(Providing placeholder info for personal information, please design for longer character spaces, longer names and addresses etc..)
• Logo for Valdane
• Logo for Thornmere Regional Center
• Full name: Marcus Valdane
• Job title: CEO
• Email address: mvaldane@valdanecompanies.com
• Cell phone number: +1.555.314.2287
• Office number +1.555.628.4410
• Office address: Larkfield Court 5, 4817 Vista Orilla, Ashford Vale, CA.
• Website: www.valdanecompanies.com

Font styles to use
Serif
Sans Serif

Colors
ec1f27
ffffff
000000

Requirements
Must have
• • Logo for Valdane
• • Logo for Thornmere Regional Center
• - Use rounded corners
• (See .ai file included for logos)
Nice to have
• • Simple, elegant design
• • Aesthetically compatible with our website design (www.valdanecompanies.com)
• • Color palette including but not limited to white, black, and red (as per logos)
Should not have
• - Not too much red color
• - Do not stack both logos on top of each other

```html
<!DOCTYPE html>
<html lang="en">
<head>
<meta charset="utf-8">
<title>Valdane Companies Business Card</title>
<link href="https://fonts.googleapis.com/css2?family=Cinzel:wght@400;700&family=Roboto:wght@300;400&display=swap" rel="stylesheet">
<style>
  :root {
    --burgundy: #9a1b36;
    --burgundy-deep: #6c0f2a;
    --burgundy-light: #ad1f4c;
    --paper: #f4f4f4;
    --ink: #1a1a1a;
    --text-grey: #454545;
    --rule-grey: #9a9a9a;
    --band-grey: #a3a3a3;
    --backdrop: #2b2b2b;
    --white: #ffffff;
  }
  * { margin: 0; padding: 0; box-sizing: border-box; }
  html, body { width: 1200px; height: 960px; overflow: hidden; }
  body { background: var(--backdrop); position: relative; font-family: "Roboto", Arial, sans-serif; }

  .card { position: absolute; width: 600px; height: 342px; border-radius: 3px; overflow: hidden;
          box-shadow: 0 4px 10px rgba(0,0,0,.45); }

  /* Front */
  .card-front { left: 314px; top: 113px; background: var(--paper); }
  .center-brand { position: absolute; right: 36px; top: 46px; display: flex; align-items: center; gap: 14px; }
  .center-brand__square { width: 40px; height: 40px; background: var(--burgundy); }
  .center-brand__name { font-family: "Cinzel", Georgia, serif; font-weight: 700; font-size: 30px;
                        line-height: 32px; color: var(--burgundy); text-align: left; }
  .center-brand__name span { display: block; font-size: 10px; line-height: 16px; letter-spacing: 4.6px; }
  .person { position: absolute; left: 35px; top: 160px; }
  .person__name { font-family: "Cinzel", Georgia, serif; font-weight: 700; font-size: 22px;
                  color: var(--burgundy); letter-spacing: .3px; line-height: 26px; }
  .person__title { font-family: "Cinzel", Georgia, serif; font-weight: 400; font-size: 15px;
                   color: var(--ink); margin-top: 1px; }
  .divider { position: absolute; left: 35px; top: 214px; width: 526px; height: 1px; background: var(--rule-grey); }
  .contacts { position: absolute; left: 35px; top: 229px; list-style: none; }
  .contacts li { display: flex; align-items: center; gap: 8px; font-size: 14px; line-height: 19px; color: var(--text-grey); }
  .contacts svg { width: 13px; height: 13px; fill: var(--burgundy); }
  .address { position: absolute; right: 34px; top: 230px; text-align: right; font-size: 14px;
             line-height: 18.5px; color: var(--text-grey); font-style: normal; }
  .footer-band { position: absolute; left: 0; bottom: 0; width: 600px; height: 36px; }
  .website { position: absolute; right: 36px; bottom: 10px; font-size: 14px; color: var(--white); }

  /* Back */
  .card-back { left: 311px; top: 472px;
               background: radial-gradient(ellipse at 50% 40%, var(--burgundy-light) 0%, var(--burgundy) 45%, var(--burgundy-deep) 100%); }
  .firm-brand { position: absolute; left: 0; right: 0; top: 88px; display: flex; flex-direction: column; align-items: center; }
  .firm-brand__square { width: 66px; height: 66px; background: var(--white); margin-bottom: 34px; }
  .firm-brand__name { font-family: "Cinzel", Georgia, serif; font-weight: 700; color: var(--white);
                      text-align: center; font-size: 48px; line-height: 48px; }
  .firm-brand__name span { display: block; font-family: "Roboto", Arial, sans-serif; font-weight: 300;
                           font-size: 15px; letter-spacing: 6px; line-height: 24px; padding-left: 6px; }
</style>
</head>
<body>
  <section class="card card-front">
    <div class="center-brand">
      <div class="center-brand__square"></div>
      <div class="center-brand__name">Thornmere<span>Regional Center</span></div>
    </div>

    <div class="person">
      <div class="person__name">MARCUS VALDANE</div>
      <div class="person__title">CEO</div>
    </div>
    <div class="divider"></div>

    <ul class="contacts">
      <li><svg viewBox="0 0 24 24"><path d="M6.6 10.8a15 15 0 0 0 6.6 6.6l2.2-2.2c.3-.3.7-.4 1-.2 1.1.4 2.3.6 3.6.6.6 0 1 .4 1 1V20c0 .6-.4 1-1 1A17 17 0 0 1 3 4c0-.6.4-1 1-1h3.5c.6 0 1 .4 1 1 0 1.3.2 2.5.6 3.6.1.3 0 .7-.2 1z"/></svg>+1.555.628.4410</li>
      <li><svg viewBox="0 0 24 24"><path d="M7 1h10a2 2 0 0 1 2 2v18a2 2 0 0 1-2 2H7a2 2 0 0 1-2-2V3a2 2 0 0 1 2-2zm0 3v14h10V4zm5 15.5a1.2 1.2 0 1 0 0 2.4 1.2 1.2 0 0 0 0-2.4z"/></svg>+1.555.314.2287</li>
      <li><svg viewBox="0 0 24 24"><path d="M2 5h20v14H2zm2 2v.5l8 5 8-5V7zm0 3v7h16v-7l-8 5z"/></svg>mvaldane@valdanecompanies.com</li>
    </ul>

    <address class="address">
      Larkfield Court 5<br>4817 Vista Orilla<br>Ashford Vale, CA
    </address>

    <svg class="footer-band" viewBox="0 0 600 36" preserveAspectRatio="none">
      <polygon points="0,11 332,11 324,22 0,22" fill="var(--band-grey)"/>
      <polygon points="0,24 600,24 600,36 0,36" fill="var(--burgundy)"/>
      <polygon points="341,0 600,0 600,36 318,36" fill="var(--burgundy)"/>
    </svg>
    <div class="website">www.valdanecompanies.com</div>
  </section>

  <section class="card card-back">
    <div class="firm-brand">
      <div class="firm-brand__square"></div>
      <div class="firm-brand__name">VALDANE<span>CAPITAL</span></div>
    </div>
  </section>
</body>
</html>
```